Business Cards Design for the electrical wholesaler: clean bold dynamic :)

We need a business card design that would follow our latest brand guidelines. As an electrical wholesaler we want to bring a fresh look and feel into the industry. The design should be clean bold and dynamic. It should come alive with the renewed energy of our green colour. Our grey colour should keep things balanced and complement the notion of maturity and responsibility. We employ Lato as a corporate font however are not bound by this font and we’re open to interpretation here.

Target Market(s)

Electrical contractors

Industry/Entity Type

Business

Contact Information for Business Card

Logo
Name & Surname: Halyna Dorosh
Job Title: Director of Marketing
Email: halya.dorosh@quillmail.example
Cell phone: XXX.XXX.XXXX
Address: 20517 - 87 Ave. Edmonton, AB, Canada. T6K 4N8
Business Phone: 780.555.0184
Website: www.brovix.example

Font styles to use
Other font styles liked:
• Lato

Requirements
Must have
• Logo & website
Nice to have
• Brand elements - some of them you may find in the attached Brand Guidelines (e.g. three lines on the background signifying "W")

```html
<!DOCTYPE html>
<html lang="en">
<head>
<meta charset="utf-8">
<title>Brovix business card</title>
<link href="https://fonts.googleapis.com/css2?family=Lato:wght@400;700;900&display=swap" rel="stylesheet">
<style>
  :root {
    --green: #8dc63f;
    --green-light: #9fd04f;
    --grey: #4d4d4f;
    --grey-soft: #5e5e60;
    --white: #ffffff;
    --page: #e9e9e7;
  }
  * { margin: 0; padding: 0; box-sizing: border-box; }
  html, body {
    width: 1200px; height: 930px; overflow: hidden;
    background: var(--page);
    font-family: "Lato", sans-serif;
  }
  .sheet { position: relative; width: 1200px; height: 930px; }
  .card {
    position: absolute; left: 240px;
    width: 720px; height: 411px; overflow: hidden;
    box-shadow: 0 6px 18px rgba(0,0,0,.15);
  }
  /* Front side */
  .card-front {
    top: 36px;
    background: linear-gradient(135deg, var(--green) 0%, var(--green-light) 100%);
  }
  .brand-lockup {
    position: absolute; left: 0; right: 0; top: 150px;
    display: flex; justify-content: center; align-items: center; gap: 16px;
  }
  .brand-dot {
    width: 34px; height: 34px; border-radius: 50%;
    background: var(--white);
  }
  .brand-name {
    font-weight: 700; font-size: 78px; line-height: 1;
    color: var(--white); letter-spacing: -1px;
  }
  .front-web {
    position: absolute; left: 0; right: 0; bottom: 44px;
    text-align: center; color: var(--white);
    font-size: 17px; letter-spacing: 1px;
  }
  /* Back side */
  .card-back { top: 483px; background: var(--white); }
  .back-lockup {
    position: absolute; right: 70px; top: 48px;
    display: flex; align-items: center; gap: 12px;
  }
  .back-lockup .brand-dot { width: 26px; height: 26px; background: var(--green); }
  .back-lockup .brand-name { font-size: 56px; color: var(--grey); }
  .divider {
    position: absolute; left: 70px; right: 70px; top: 178px;
    height: 1.5px; background: var(--green);
  }
  .person { position: absolute; left: 70px; top: 120px; }
  .person-name {
    font-weight: 700; font-size: 27px; color: var(--green); line-height: 1.1;
  }
  .person-title { font-size: 17px; color: var(--grey); margin-top: 2px; }
  .address {
    position: absolute; right: 70px; top: 192px;
    text-align: right; font-size: 17px; color: var(--grey); line-height: 1.3;
  }
  .contacts {
    position: absolute; left: 70px; top: 200px;
    list-style: none; font-size: 17px; color: var(--grey);
  }
  .contacts li { display: flex; align-items: center; gap: 12px; line-height: 1.45; }
  .contacts svg { width: 13px; height: 13px; flex: none; }
  .contacts .accent { color: var(--green); }
  .wave { position: absolute; left: 0; bottom: 0; width: 720px; height: 411px; }
</style>
</head>
<body>
<main class="sheet">
  <section class="card card-front" aria-label="Card front">
    <div class="brand-lockup">
      <span class="brand-dot"></span>
      <span class="brand-name">brovix</span>
    </div>
    <p class="front-web">www.brovix.example</p>
  </section>

  <section class="card card-back" aria-label="Card back">
    <svg class="wave" viewBox="0 0 720 411" aria-hidden="true">
      <path d="M0 411 L0 404 C100 334 220 346 360 346 C520 346 640 332 720 298 L720 411 Z" fill="var(--green)"/>
      <path d="M28 398 C110 330 220 334 360 334 C520 334 640 318 714 286" fill="none" stroke="var(--grey-soft)" stroke-width="6" stroke-linecap="round"/>
    </svg>

    <div class="back-lockup">
      <span class="brand-dot"></span>
      <span class="brand-name">brovix</span>
    </div>

    <div class="person">
      <p class="person-name">Halyna Dorosh</p>
      <p class="person-title">Director of Marketing</p>
    </div>

    <div class="divider"></div>

    <p class="address">20517 87ave<br>T6K4N8 Edmonton,<br>Alberta</p>

    <ul class="contacts">
      <li>
        <svg viewBox="0 0 16 16" aria-hidden="true"><path d="M4 1l3 3-2 2c1 2 3 4 5 5l2-2 3 3-2 3C7 15 1 9 1 3z" fill="var(--green)"/></svg>
        780.555.0184
      </li>
      <li>
        <svg viewBox="0 0 16 16" aria-hidden="true"><rect x="1" y="3" width="14" height="10" fill="none" stroke="var(--green)" stroke-width="1.6"/><path d="M1 3l7 6 7-6" fill="none" stroke="var(--green)" stroke-width="1.6"/></svg>
        halya.dorosh@quillmail.example
      </li>
      <li>
        <svg viewBox="0 0 16 16" aria-hidden="true"><circle cx="8" cy="8" r="6.5" fill="none" stroke="var(--green)" stroke-width="1.5"/><ellipse cx="8" cy="8" rx="2.8" ry="6.5" fill="none" stroke="var(--green)" stroke-width="1.2"/><path d="M1.5 8h13" stroke="var(--green)" stroke-width="1.2"/></svg>
        <span>www.<span class="accent">brovix</span>.example</span>
      </li>
    </ul>
  </section>
</main>
</body>
</html>
```